Business Card Design

We provide services doing multiple jobs in the construction industry.Please note: The company name needs to be ROCK SOLID BUILDING SERVICESAttached logo was an example of what we wanted. Can you change up the colors?

Industry/Entity Type

Construction

Contact Information for Business Card

ROCK SOLID BUILDING SERVICES5401 HUDSON BEND RDAUSTIN, TX 78734(512)243-6854ROCKSOLIDBUILDINGSERVICES@GMAIL.COM

```html
<!DOCTYPE html>
<html lang="en">
<head>
<meta charset="utf-8">
<title>Pearlwood Framing Works — Business Card</title>
<link rel="stylesheet" href="https://fonts.googleapis.com/css2?family=Exo+2:wght@700&family=Arimo:wght@400&display=swap">
<style>
  :root {
    --page-bg: #e9e7e3;
    --card-bg: #ffffff;
    --ink-navy: #25235e;
    --ink-black: #111111;
    --rule: #2a2866;
  }
  html, body {
    margin: 0;
    width: 1200px;
    height: 800px;
    overflow: hidden;
    background: var(--page-bg);
  }
  .card {
    position: absolute;
    left: 75px;
    top: 100px;
    width: 1050px;
    height: 600px;
    background: var(--card-bg);
    box-shadow: 0 2px 10px rgba(0,0,0,0.12);
  }
  .company-name {
    position: absolute;
    left: 60px;
    top: 150px;
    margin: 0;
    font-family: "Exo 2", sans-serif;
    font-weight: 700;
    font-size: 34px;
    letter-spacing: 0.5px;
    color: var(--ink-black);
  }
  .title-rule {
    position: absolute;
    left: 50px;
    top: 212px;
    width: 930px;
    height: 2px;
    background: var(--rule);
  }
  .brand-mark {
    position: absolute;
    right: 70px;
    top: 100px;
    display: flex;
    align-items: center;
    gap: 14px;
  }
  .brand-mark .mark-square {
    width: 34px;
    height: 34px;
    background: var(--ink-navy);
  }
  .brand-mark .mark-name {
    font-family: "Exo 2", sans-serif;
    font-weight: 700;
    font-size: 52px;
    color: var(--ink-navy);
  }
  .contact-list {
    position: absolute;
    left: 60px;
    top: 262px;
    margin: 0;
    padding: 0;
    list-style: none;
    font-family: "Arimo", sans-serif;
    font-size: 26px;
    color: var(--ink-navy);
  }
  .contact-list li {
    display: flex;
    align-items: center;
    gap: 14px;
    height: 40px;
  }
  .contact-list svg { width: 20px; height: 20px; fill: var(--ink-navy); flex: none; }
  .address {
    position: absolute;
    right: 80px;
    top: 430px;
    margin: 0;
    text-align: right;
    font-family: "Arimo", sans-serif;
    font-style: normal;
    font-size: 28px;
    line-height: 38px;
    color: var(--ink-navy);
  }
</style>
</head>
<body>
  <section class="card">
    <h1 class="company-name">PEARLWOOD FRAMING WORKS</h1>
    <div class="title-rule"></div>

    <div class="brand-mark">
      <span class="mark-square"></span>
      <span class="mark-name">PEARLWOOD</span>
    </div>

    <ul class="contact-list">
      <li>
        <svg viewBox="0 0 24 24" aria-hidden="true"><path d="M6.6 10.8a15 15 0 0 0 6.6 6.6l2.2-2.2a1 1 0 0 1 1-.25 11.4 11.4 0 0 0 3.6.57 1 1 0 0 1 1 1V20a1 1 0 0 1-1 1A17 17 0 0 1 3 4a1 1 0 0 1 1-1h3.5a1 1 0 0 1 1 1c0 1.25.2 2.45.57 3.57a1 1 0 0 1-.25 1z"/></svg>
        <span>(512)555-0193</span>
      </li>
      <li>
        <svg viewBox="0 0 24 24" aria-hidden="true"><path d="M2 5h20v14H2zm2 2v.5l8 5 8-5V7zm0 2.8V17h16V9.8l-8 5z"/></svg>
        <span>Pearlwoodframingworks@mailnest.example</span>
      </li>
    </ul>

    <address class="address">
      7732 Fernglen Pass LN<br>
      Austin, TX 78799
    </address>
  </section>
</body>
</html>
```